GJ & DW Fencing Pty Ltd

We already have an existing logo created by Pixel Harbour however we have restructured to a company. We would like someone to add Pty Ltd to our business name please.

Colors

Designer to choose only greyscale colors for use in the design.

```html
<!DOCTYPE html>
<html lang="en">
<head>
<meta charset="utf-8">
<title>GJ &amp; DW Fencing Pty Ltd – Business Card</title>
<link href="https://fonts.googleapis.com/css2?family=Cinzel:wght@400;600&family=Raleway:wght@400&display=swap" rel="stylesheet">
<style>
  :root {
    --page-bg: #d9d9d9;
    --card-dark: #0e0e0e;
    --card-mid: #2a2a2a;
    --card-sheen: #4a4a4a;
    --ink-light: #f2f2f2;
    --ink-soft: #cfcfcf;
    --rule: #bdbdbd;
    --icon-glyph: #1a1a1a;
  }
  html, body {
    margin: 0;
    width: 1200px;
    height: 1022px;
    overflow: hidden;
    background: var(--page-bg);
  }
  .stage {
    width: 1200px;
    height: 1022px;
    display: flex;
    align-items: center;
    justify-content: center;
  }
  .business-card {
    position: relative;
    width: 840px;
    height: 480px;
    border-radius: 22px;
    background:
      linear-gradient(125deg, transparent 35%, rgba(255,255,255,0.10) 48%, transparent 62%),
      radial-gradient(ellipse at 40% 55%, var(--card-sheen) 0%, var(--card-mid) 35%, var(--card-dark) 80%);
    box-shadow: 0 18px 40px rgba(0,0,0,0.35);
    color: var(--ink-light);
    overflow: hidden;
  }
  .brand {
    position: absolute;
    left: 60px;
    top: 70px;
    display: flex;
    align-items: center;
    gap: 18px;
  }
  .brand-dot {
    width: 56px;
    height: 56px;
    border-radius: 50%;
    background: var(--ink-light);
    flex: none;
  }
  .brand-name {
    font-family: "Cinzel", serif;
    font-weight: 600;
    font-size: 38px;
    line-height: 1.1;
    color: var(--ink-light);
    letter-spacing: 1px;
  }
  .divider {
    position: absolute;
    left: 60px;
    right: 60px;
    top: 230px;
    height: 1.5px;
    background: var(--rule);
  }
  .holder-name {
    position: absolute;
    left: 60px;
    top: 262px;
    font-family: "Cinzel", serif;
    font-weight: 400;
    font-size: 26px;
    letter-spacing: 5px;
    color: var(--ink-soft);
    margin: 0;
  }
  .contact-list {
    position: absolute;
    right: 60px;
    top: 258px;
    margin: 0;
    padding: 0;
    list-style: none;
    font-family: "Raleway", sans-serif;
    font-size: 21px;
    color: var(--ink-light);
  }
  .contact-item {
    display: flex;
    align-items: center;
    justify-content: flex-end;
    gap: 16px;
    height: 44px;
  }
  .contact-icon {
    width: 26px;
    height: 26px;
    flex: none;
  }
</style>
</head>
<body>
<main class="stage">
  <section class="business-card" aria-label="Business card, GJ &amp; DW Fencing Pty Ltd">
    <div class="brand">
      <span class="brand-dot" aria-hidden="true"></span>
      <span class="brand-name">GJ &amp; DW<br>Fencing Pty Ltd</span>
    </div>
    <div class="divider"></div>
    <p class="holder-name">SAM WHITFORD</p>
    <ul class="contact-list">
      <li class="contact-item">
        <span>PO Box 418 Carrow WA 6512</span>
        <svg class="contact-icon" viewBox="0 0 26 26" aria-hidden="true">
          <circle cx="13" cy="13" r="13" fill="var(--ink-light)"/>
          <path d="M6.5 13 L13 7 L19.5 13 M8.5 12 V19 H17.5 V12" fill="none" stroke="var(--icon-glyph)" stroke-width="1.8" stroke-linejoin="round"/>
        </svg>
      </li>
      <li class="contact-item">
        <span>0455 210 947</span>
        <svg class="contact-icon" viewBox="0 0 26 26" aria-hidden="true">
          <circle cx="13" cy="13" r="13" fill="var(--ink-light)"/>
          <path d="M9 7 L11.5 7 L12.5 10.5 L11 11.8 C11.8 13.6 12.6 14.4 14.2 15.1 L15.5 13.6 L19 14.6 L19 17 C19 18 18 19 17 19 C12 18.6 7.4 14 7 9 C7 8 8 7 9 7 Z" fill="var(--icon-glyph)"/>
        </svg>
      </li>
      <li class="contact-item">
        <span>gjdwfencing@fieldmail.com</span>
        <svg class="contact-icon" viewBox="0 0 26 26" aria-hidden="true">
          <circle cx="13" cy="13" r="13" fill="var(--ink-light)"/>
          <rect x="6.5" y="8.5" width="13" height="9" fill="none" stroke="var(--icon-glyph)" stroke-width="1.6"/>
          <path d="M6.5 8.5 L13 13.5 L19.5 8.5" fill="none" stroke="var(--icon-glyph)" stroke-width="1.6"/>
        </svg>
      </li>
    </ul>
  </section>
</main>
</body>
</html>
```